Nutrition business needs logo & business card design

We need a business card & logo design for a new company based in Toronto, Ontario Canada called Verdel Wellworks.

We provide nutrition service using metrics as guide to manage client's progress. Our service creates individualized nutrition and lifestyle strategies that focuses on improving Performance, Longevity and Weight Loss. I would like to see designs that use the color of green, gray, blue and white.

The final design should:

--convey a feeling of connectedness with positive transformation.

-- communicate the idea of awareness with guided effort that yields personal independence for a better and more productive life

Target Market(s)

Professionals who work in the IT/Computer/Engineering/Banking industry specifically Directors, Managers, CEO's.

Industry/Entity Type

Health And Wellness

Contact Information for Business Card

Dorvane Pike, Owner
email: DPIKE@verdelwellworks.example
tel: - 555-204-7718

Logo Text

better health through analytics or measure to manage

Font styles to use
Other font styles liked:
• Garamound

Colors
ffffff
abd037
85acd3
757575
34a7d7

Requirements
Must have
• Good contrast and decent size font - ease of readability, aesthetically nice colors
Nice to have
• image of chart or graph that conveys measurement or analytics
Should not have
• Borders, images of food,

```html
<!DOCTYPE html>
<html lang="en">
<head>
<meta charset="utf-8">
<title>Verdel Wellworks — Business Card</title>
<link rel="stylesheet" href="https://fonts.googleapis.com/css2?family=Source+Sans+3:wght@400;600&display=swap">
<style>
  :root {
    --brand-blue: #0a84ff;
    --brand-green: #33aa00;
    --paper: #ffffff;
    --backdrop: #ecebe8;
    --ink-light: #ffffff;
  }
  * { margin: 0; padding: 0; box-sizing: border-box; }
  html, body {
    width: 1200px; height: 900px; overflow: hidden;
    background: var(--backdrop);
    font-family: "Source Sans 3", "Myriad Pro", Arial, sans-serif;
  }
  .card {
    position: absolute;
    overflow: hidden;
    box-shadow: 0 6px 18px rgba(0,0,0,.18);
  }
  .card-front { left: 78px; top: 34px; width: 588px; height: 364px; background: var(--paper); }
  .card-back  { left: 388px; top: 505px; width: 567px; height: 352px; background: var(--brand-blue); }
  .card-shapes { position: absolute; inset: 0; }

  .brand-mark { position: absolute; border-radius: 50%; }
  .card-front .brand-mark { left: 81px; top: 49px; width: 110px; height: 110px; border: 6px solid var(--brand-blue); }
  .card-back .brand-mark  { left: 95px; top: 125px; width: 100px; height: 100px; border: 6px solid var(--ink-light); }

  .brand-name { position: absolute; white-space: nowrap; font-weight: 400; letter-spacing: -0.5px; }
  .card-front .brand-name { left: 216px; top: 76px; font-size: 43px; color: var(--brand-blue); }
  .card-back .brand-name  { left: 214px; top: 152px; font-size: 37px; color: var(--ink-light); }

  .holder { position: absolute; right: 316px; top: 262px; text-align: right; color: var(--ink-light); }
  .holder-name { font-size: 21px; font-weight: 600; line-height: 24px; }
  .holder-role { font-size: 16px; line-height: 22px; }

  .contact-list { position: absolute; left: 294px; top: 250px; list-style: none; color: var(--ink-light); font-size: 16px; }
  .contact-list li { display: flex; align-items: center; height: 21px; }
  .contact-list svg { width: 12px; height: 12px; margin-right: 12px; fill: var(--ink-light); }

  .address { position: absolute; left: 103px; top: 328px; font-size: 16px; color: var(--ink-light); white-space: nowrap; }
</style>
</head>
<body>

<section class="card card-front" aria-label="Business card front">
  <svg class="card-shapes" viewBox="0 0 588 364" aria-hidden="true">
    <polygon points="0,228 380,228 412,191 588,191 588,364 0,364" fill="var(--brand-blue)"/>
    <polygon points="0,199 402,199 379,226 0,226" fill="var(--brand-green)"/>
  </svg>
  <div class="brand-mark" aria-hidden="true"></div>
  <div class="brand-name">Verdel Wellworks</div>

  <div class="holder">
    <div class="holder-name">Dorvane Pike</div>
    <div class="holder-role">Managing Director</div>
  </div>

  <ul class="contact-list">
    <li><svg viewBox="0 0 24 24"><path d="M6.6 10.8a15 15 0 0 0 6.6 6.6l2.2-2.2c.3-.3.7-.4 1-.2 1.1.4 2.3.6 3.6.6.6 0 1 .4 1 1V20c0 .6-.4 1-1 1A17 17 0 0 1 3 4c0-.6.4-1 1-1h3.5c.6 0 1 .4 1 1 0 1.3.2 2.5.6 3.6.1.3 0 .7-.2 1z"/></svg>555-204-7718</li>
    <li><svg viewBox="0 0 24 24"><path d="M2 5h20v14H2z M3.5 6.5 12 13l8.5-6.5" fill="var(--ink-light)" stroke="var(--brand-blue)" stroke-width="1.6"/></svg>info@verdelwellworks.example</li>
    <li><svg viewBox="0 0 24 24"><circle cx="12" cy="12" r="9.5" fill="none" stroke="var(--ink-light)" stroke-width="2"/><path d="M2.5 12h19M12 2.5c3 3 3 16 0 19M12 2.5c-3 3-3 16 0 19" fill="none" stroke="var(--ink-light)" stroke-width="1.6"/></svg>www.verdelwellworks.example</li>
  </ul>

  <div class="address">48 Harbour Lane, Toronto, Ontario Canada, M5V 2T6.</div>
</section>

<section class="card card-back" aria-label="Business card back">
  <div class="brand-mark" aria-hidden="true"></div>
  <div class="brand-name">Verdel Wellworks</div>
</section>

</body>
</html>
```